Presentation Brochure and Sample Box Design for Kovo Slate

Kovo Slate is a colour coated solid aluminium panel that our company supplies to the signage and building cladding industries.
We require an, A4 double-sided folding brochure (swatch book) that folds 3 ways, opening once and then a second time to lay out 3 pages flat.

There should be a front and back cover.

The inside cover should be reserved with text blocks for written information about the panel.

The opposite page on the right when you first open the brochure should have all our Matte PVDF 2mm colours which you will find in the attached PDF of colour swatches and details.

When the brochure is folded out a second time, showing all three inside pages flat, the two inside pages on the right (next to the inside cover with the written information) should show all our FEVE Gloss 1.6mm colours which you will also find in the attached PDF colour book.

This brochure should have a modern and professional feel suitable for presenting to architects and designers.

We also require a box design to contain aluminium samples of all the colours in the range.

Please refer to the template attached for the box dimensions and layout.

The box should tie in with the brochure as a complete package with a modern and professional look suitable for presenting to architects and designers.

Finally we require a small label sticker to be stuck on the back of each sample. On the sticker should be the Kovo Slate logo, a space to put the product code for the sample colour and the phone number 1300 584 362.

To summarise, this package project includes:
1 tri-folding A4 brochure,
1 sample box package design,
1 sample sticker label.

This is our signature new product that we will be marketing to signage installers to create coloured and printed aluminium signs. We are also looking to move further into the building and architectural market place with this product.

Please refer to the attachments for the Kovo Slate logo - the colour swatch book and template for the sample box.
The Kovo Slate logo can be shown in White, Black or Silver.

Target Market(s)

Architects, interior designers, builders and signage installers.

Font styles to use
Serif
Sans Serif

Requirements
Must have
• A modern, neat and professional upmarket look suitable for presenting to architects.
Nice to have
• A slick and classy look that makes you want to take home the box or brochure even if you're not interested in the product.
Should not have
• A cheap, untidy, low market look with too many colours.

```html
<!DOCTYPE html>
<html lang="en">
<head>
<meta charset="utf-8">
<title>Kovo Slate – Brochure, Box and Sticker Presentation</title>
<link href="https://fonts.googleapis.com/css2?family=Barlow:wght@400;500;600;700&family=Barlow+Condensed:wght@300;400;600;700&display=swap" rel="stylesheet">
<style>
  :root{
    --board:#f1f1f2;
    --sidebar:#c8c9ce;
    --sidebar-text:#5a5c63;
    --ink:#23232d;
    --paper:#ffffff;
    --paper-shade:#ececee;
    --frame:#d0d0d3;
    --muted:#8a8b90;
    --accent:#f7941d;
    --scene:#5d6070;
    --scene-dark:#1f2130;
    --cream:#efece4;
    --sticker:#2d303c;
  }
  *{box-sizing:border-box;margin:0;padding:0}
  html,body{width:720px;height:1200px;overflow:hidden;background:var(--board)}
  body{position:relative;font-family:"Barlow",sans-serif;color:var(--ink)}
  .abs{position:absolute}

  /* sidebar */
  .sidebar{position:absolute;left:662px;top:0;width:58px;height:1200px;background:var(--sidebar)}
  .side-label{position:absolute;left:690px;transform:translate(-50%,-50%) rotate(90deg);white-space:nowrap;
    font-family:"Barlow Condensed",sans-serif;font-weight:700;font-size:17px;letter-spacing:.5px;color:var(--sidebar-text)}

  /* swatches */
  .swatch{position:absolute;width:27px;height:27px;border-radius:2px;background:var(--c);
    box-shadow:0 2px 3px rgba(0,0,0,.18);display:flex;align-items:flex-end;justify-content:center;
    padding-bottom:4px;text-align:center;font-family:"Barlow Condensed",sans-serif;font-weight:600;
    font-size:3.6px;line-height:1.1;color:#fff;text-transform:uppercase}
  .swatch.dark-text{color:#2a2a2a}
  .swatch.mid{align-items:center;padding-bottom:0}

  /* outer spread */
  .outer{position:absolute;left:27px;top:29px;width:602px;height:283px;background:var(--paper);box-shadow:0 6px 14px rgba(0,0,0,.12)}
  .swatch-page{position:absolute;left:0;top:0;width:203px;height:283px;background:#f6f6f7}
  .swatch-frame{position:absolute;left:10px;top:9px;width:184px;height:264px;border:1.5px solid var(--frame);border-radius:6px;overflow:hidden}
  .metal-zone{position:absolute;left:0;bottom:0;width:100%;height:86px;background:var(--paper-shade)}
  .page-head{position:absolute;display:flex;justify-content:space-between;align-items:flex-end;
    font-family:"Barlow Condensed",sans-serif;border-bottom:.6px solid currentColor;padding-bottom:1px}
  .page-head .range{font-weight:300;font-size:7px}
  .page-head .finish{font-weight:700;font-size:7.5px}
  .vertical-name{position:absolute;transform:rotate(-90deg);transform-origin:left top;font-weight:600;font-size:11px;letter-spacing:.5px;color:var(--ink)}
  .cover-right{position:absolute;left:402px;top:0;width:200px;height:283px;background:linear-gradient(180deg,#e4e4e6,#fafafa 60%)}
  .brand{font-family:"Barlow",sans-serif;font-weight:600;letter-spacing:1px;color:var(--ink);white-space:nowrap}

  /* inner spread */
  .inner{position:absolute;left:27px;top:373px;width:603px;height:284px;background:var(--ink);box-shadow:0 6px 14px rgba(0,0,0,.2)}
  .intro-title{position:absolute;left:19px;top:143px;font-size:22px;font-weight:600;color:#fff;letter-spacing:.5px}
  .intro-copy{position:absolute;left:19px;top:178px;width:140px;color:#e6e6ea;font-size:4.4px;line-height:6px;text-align:justify}
  .intro-copy p+p{margin-top:5px}
  .drop{float:left;font-size:15px;line-height:12px;font-weight:600;margin-right:2px;color:#fff}
  .gloss-frame{position:absolute;top:10px;width:186px;height:265px;border:1.5px solid #fff;border-radius:6px}
  .gloss-frame .page-head{color:#fff}
  .gloss-note{position:absolute;right:12px;text-align:right;font-family:"Barlow Condensed",sans-serif;color:#fff;line-height:1.2}
  .gloss-note .range{font-weight:300;font-size:5.5px;display:block}
  .gloss-note .finish{font-weight:700;font-size:5.5px}

  /* mockup area */
  .scene{position:absolute;overflow:hidden}
  .scene-caption{position:absolute;left:0;width:100%;height:27px;background:var(--scene-dark);color:#fff;
    font-size:7px;letter-spacing:.4px;display:flex;align-items:center;padding:0 15px}
  .box-face{position:absolute;border-radius:2px;overflow:hidden;box-shadow:0 8px 14px rgba(0,0,0,.3)}
  .box-face.dark{background:#272a3b;color:#fff}
  .box-face.light{background:#f4f4f6;color:var(--ink)}
  .box-name{position:absolute;font-weight:600;font-size:11px;letter-spacing:.6px}
  .box-title{position:absolute;font-size:10px;line-height:11px;font-weight:400;letter-spacing:.3px}
  .box-title strong{display:block;font-weight:700;color:var(--accent)}
  .box-fine{position:absolute;font-size:4.5px;line-height:6px;opacity:.75;width:90px}
  .mosaic{position:absolute;display:grid;grid-template-columns:repeat(4,9px);gap:2px}
  .mosaic i{display:block;width:9px;height:9px;border-radius:1px;background:var(--c)}
  .label-panel{position:absolute;top:0;right:0;width:52px;height:100%;background:#fff;color:var(--ink)}
  .dark-panel{position:absolute;top:0;right:0;width:52px;height:100%;background:#2d3041;color:#fff}

  /* stickers */
  .sticker{position:absolute;width:75px;height:65px;background:var(--sticker);color:#fff;box-shadow:0 3px 6px rgba(0,0,0,.18)}
  .sticker .brand{position:absolute;right:6px;top:5px;color:#fff;font-size:5.5px}
  .sticker .code{position:absolute;left:0;width:100%;top:23px;text-align:center;font-weight:700;font-size:14px}
  .sticker .phone{position:absolute;left:5px;bottom:6px;font-size:3.4px}
  .sticker .hint{position:absolute;width:100%;top:41px;text-align:center;font-size:3px;opacity:.6}
  .option{position:absolute;font-size:5px;font-weight:600;color:#333;letter-spacing:.3px}
</style>
</head>
<body>

<!-- Sidebar -->
<div class="sidebar"></div>
<div class="side-label" style="top:185px">BROCHURE DESIGN</div>
<div class="side-label" style="top:812px">MOCKUP</div>
<div class="side-label" style="top:1070px">STICKER LABEL DESIGN</div>

<!-- Outer spread: PVDF page + cover -->
<section class="outer">
  <div class="swatch-page">
    <div class="swatch-frame">
      <div class="metal-zone"></div>
      <div class="page-head" style="left:8px;top:7px;width:166px"><span class="range">COLOUR COATED SOLID ALUMINIUM</span><span class="finish">PVDF MATTE 2MM</span></div>

      <div class="swatch" style="left:12px;top:24px;--c:#b3182a">PVDF MATTE<br>PLUM RED</div>
      <div class="swatch" style="left:47px;top:24px;--c:#cf1f2e">PVDF MATTE<br>RED</div>
      <div class="swatch" style="left:81px;top:24px;--c:#e3541f">PVDF MATTE<br>ORANGE</div>
      <div class="swatch dark-text" style="left:116px;top:24px;--c:#eaa51c">PVDF MATTE<br>MUSTARD</div>

      <div class="swatch dark-text" style="left:12px;top:58px;--c:#d8c89a">PVDF MATTE<br>IVORY</div>
      <div class="swatch" style="left:47px;top:58px;--c:#1b2240">PVDF MATTE<br>NAVY BLUE</div>
      <div class="swatch" style="left:81px;top:58px;--c:#202446">PVDF MATTE<br>GALAXY</div>
      <div class="swatch" style="left:116px;top:58px;--c:#28307a">PVDF MATTE<br>REFLEX BLUE</div>

      <div class="swatch" style="left:12px;top:93px;--c:#2c323a">PVDF MATTE<br>STEEL GREY</div>
      <div class="swatch" style="left:47px;top:93px;--c:#5a5f66">PVDF MATTE<br>IRON GREY</div>
      <div class="swatch" style="left:81px;top:93px;--c:#8e9094">PVDF MATTE<br>WARM GREY</div>
      <div class="swatch dark-text" style="left:116px;top:93px;--c:#b6b7b9">PVDF MATTE<br>SMOKEY GREY</div>

      <div class="swatch dark-text" style="left:12px;top:127px;--c:#d6cfc5">PVDF MATTE<br>CREAM</div>
      <div class="swatch" style="left:47px;top:127px;--c:#050505">PVDF MATTE<br>BLACK</div>
      <div class="swatch dark-text" style="left:81px;top:127px;--c:#ffffff">PVDF MATTE<br>WHITE</div>

      <div class="swatch mid dark-text" style="left:12px;top:181px;--c:#a9abad">PVDF<br>METALLIC<br>SILVER</div>
      <div class="swatch mid" style="left:47px;top:181px;--c:#2a2a2c">PVDF<br>METALLIC<br>CHARCOAL</div>
      <div class="swatch mid dark-text" style="left:81px;top:181px;--c:#c9a63b">PVDF<br>METALLIC<br>GOLD</div>
      <div class="swatch mid dark-text" style="left:12px;top:216px;--c:#f2e21b">PVDF<br>METALLIC<br>YELLOW</div>
      <div class="swatch mid" style="left:47px;top:216px;--c:#1e6aa0">PVDF<br>METALLIC<br>BLUE</div>

      <div class="vertical-name" style="left:160px;top:254px">Kovo Slate</div>
    </div>
  </div>

  <div class="cover-right"></div>
  <svg class="abs" style="left:203px;top:0" width="399" height="283" role="img" aria-label="Photograph of a glass office tower seen from below, rising to a sharp point">
    <defs>
      <linearGradient id="tower" x1="0" y1="1" x2="0" y2="0">
        <stop offset="0" stop-color="#b8b9bc"/>
        <stop offset="1" stop-color="#dcdcde"/>
      </linearGradient>
    </defs>
    <polygon points="52,283 199,62 346,283" fill="url(#tower)"/>
  </svg>
  <div class="brand abs" style="left:270px;top:240px;font-size:13px">Kovo Slate</div>
  <div class="brand abs" style="left:505px;top:40px;font-size:13px">Kovo Slate</div>
</section>

<!-- Inner spread: intro + FEVE gloss pages -->
<section class="inner">
  <svg class="abs" style="left:28px;top:22px" width="124" height="93" role="img" aria-label="Photograph of a modern building facade clad in red and charcoal aluminium panels">
    <rect x="0" y="0" width="124" height="93" fill="#c85a4c"/>
    <rect x="4" y="4" width="116" height="85" rx="4" fill="#3a3c44"/>
  </svg>
  <div class="intro-title">Kovo Slate</div>
  <div class="intro-copy">
    <p><span class="drop">A</span><strong>Kovo Slate</strong> convallis nisi eu tortor facilisis pulvinar. Aenean vitae augue in risus maximus hendrerit. Aliquam lectus metus, lacinia itae elit ut, posuere facilisis dolor. Ut quis felis in sem pellentesque iaculis. Etiam ac ex a leo vestibulum condimentum. Curabitur hendrerit urna eros, non semper nibh placerat ut. Etiam ultrices, magna eu blandit venenatis, ipsum lectus aliquam turpis, sit amet convallis dui mi nec neque. In semper tristique luctus. Nunc et lorem ex. Ut scelerisque ex augue, eget faucibus odio rutrum ut.</p>
    <p>Curabitur hendrerit urna eros, non semper nibh placerat ut. Etiam ultrices, magna eu blandit venenatis, ipsum lectus aliquam turpis, sit amet convallis dui mi nec neque. In semper tristique luctus.</p>
  </div>

  <div class="gloss-frame" style="left:208px">
    <div class="page-head" style="left:16px;top:9px;width:156px"><span class="range">COLOUR COATED SOLID ALUMINIUM</span><span class="finish">FEVE GLOSS 1.6MM</span></div>

    <div class="swatch" style="left:22px;top:33px;--c:#ee3e4a">FEVE GLOSS<br>WARM RED</div>
    <div class="swatch" style="left:59px;top:33px;--c:#da1f31">FEVE GLOSS<br>RED</div>
    <div class="swatch" style="left:96px;top:33px;--c:#c61a35">FEVE GLOSS<br>PLUM RED</div>
    <div class="swatch" style="left:133px;top:33px;--c:#7a1b2a">FEVE GLOSS<br>HERITAGE RED</div>

    <div class="swatch" style="left:22px;top:70px;--c:#f05a2a">FEVE GLOSS<br>ORANGE</div>
    <div class="swatch" style="left:59px;top:70px;--c:#f27e3e">FEVE GLOSS<br>PUMPKIN</div>
    <div class="swatch" style="left:96px;top:70px;--c:#f7941d">FEVE GLOSS<br>TANGERINE</div>
    <div class="swatch" style="left:133px;top:70px;--c:#fbb126">FEVE GLOSS<br>MUSTARD</div>

    <div class="swatch dark-text" style="left:22px;top:107px;--c:#fbe51a">FEVE GLOSS<br>YELLOW</div>
    <div class="swatch dark-text" style="left:59px;top:107px;--c:#fde046">FEVE GLOSS<br>LEMON<br>MERINGUE</div>
    <div class="swatch" style="left:96px;top:107px;--c:#9bc63f">FEVE GLOSS<br>LIME GREEN</div>
    <div class="swatch" style="left:133px;top:107px;--c:#3bad4a">FEVE GLOSS<br>APPLE GREEN</div>

    <div class="swatch" style="left:22px;top:144px;--c:#5aa845">FEVE GLOSS<br>SPRING GREEN</div>
    <div class="swatch" style="left:59px;top:144px;--c:#0ea44a">FEVE GLOSS<br>GREEN</div>
    <div class="swatch" style="left:96px;top:144px;--c:#0b8f51">FEVE GLOSS<br>EMERALD</div>
    <div class="swatch" style="left:133px;top:144px;--c:#12473a">FEVE GLOSS<br>FOREST GREEN</div>

    <div class="swatch" style="left:22px;top:181px;--c:#5e8c72">FEVE GLOSS<br>OLIVE GREEN</div>
    <div class="swatch" style="left:59px;top:181px;--c:#11938a">FEVE GLOSS<br>MINT</div>
    <div class="swatch" style="left:96px;top:181px;--c:#0a7d93">FEVE GLOSS<br>TURQUOISE</div>
    <div class="swatch" style="left:133px;top:181px;--c:#0b4c5a">FEVE GLOSS<br>TEAL</div>

    <div class="swatch" style="left:22px;top:218px;--c:#1287c9">FEVE GLOSS<br>PROCESS BLUE</div>
    <div class="swatch" style="left:59px;top:218px;--c:#0c4f85">FEVE GLOSS<br>LAGOON</div>
    <div class="swatch" style="left:96px;top:218px;--c:#1745a0">FEVE GLOSS<br>PATRIOTIC BLUE</div>
    <div class="swatch" style="left:133px;top:218px;--c:#232f7a">FEVE GLOSS<br>REFLEX BLUE</div>
  </div>

  <div class="gloss-frame" style="left:408px">
    <div class="swatch" style="left:24px;top:7px;--c:#22285a">FEVE GLOSS<br>GALAXY</div>
    <div class="swatch" style="left:60px;top:7px;--c:#1c2a4e">FEVE GLOSS<br>NAVY BLUE</div>
    <div class="swatch" style="left:96px;top:7px;--c:#222157">FEVE GLOSS<br>ROYAL BLUE</div>
    <div class="swatch" style="left:132px;top:7px;--c:#60676d">FEVE GLOSS<br>IRON GREY</div>

    <div class="swatch" style="left:24px;top:43px;--c:#86bfdf">FEVE GLOSS<br>BABY BLUE</div>
    <div class="swatch" style="left:60px;top:43px;--c:#e38fbd">FEVE GLOSS<br>PINK</div>
    <div class="swatch" style="left:96px;top:43px;--c:#e3237a">FEVE GLOSS<br>FUCHSIA</div>
    <div class="swatch" style="left:132px;top:43px;--c:#a52a8c">FEVE<br>MULBERRY</div>

    <div class="swatch" style="left:24px;top:79px;--c:#5e3591">FEVE<br>VIOLET</div>
    <div class="swatch" style="left:60px;top:79px;--c:#3d2a84">FEVE<br>PURPLE</div>
    <div class="swatch" style="left:96px;top:79px;--c:#3b3058">FEVE GLOSS<br>MIDNIGHT<br>PURPLE</div>
    <div class="swatch" style="left:132px;top:79px;--c:#7e4595">FEVE GLOSS<br>VIOLET</div>

    <div class="swatch dark-text" style="left:24px;top:115px;--c:#d9c99d">FEVE GLOSS<br>IVORY</div>
    <div class="swatch dark-text" style="left:60px;top:115px;--c:#cbc3b5">HIGH GLOSS<br>CREAM</div>
    <div class="swatch dark-text" style="left:96px;top:115px;--c:#b9b9bb">FEVE GLOSS<br>SMOKEY GREY</div>
    <div class="swatch" style="left:132px;top:115px;--c:#aea08d">FEVE GLOSS<br>LATTE</div>

    <div class="swatch" style="left:24px;top:151px;--c:#8f8174">FEVE GLOSS<br>STONE</div>
    <div class="swatch" style="left:60px;top:151px;--c:#6e5a52">FEVE GLOSS<br>MOCHA</div>
    <div class="swatch" style="left:96px;top:151px;--c:#5a3f43">FEVE GLOSS<br>AUBERGINE</div>
    <div class="swatch" style="left:132px;top:151px;--c:#6d3331">FEVE GLOSS<br>MILK CHOCOLATE</div>

    <div class="swatch" style="left:24px;top:187px;--c:#5c2427">FEVE GLOSS<br>RUST</div>
    <div class="swatch" style="left:60px;top:187px;--c:#2e3640">FEVE GLOSS<br>STEEL GREY</div>
    <div class="swatch" style="left:96px;top:187px;--c:#8e9195">HIGH GLOSS<br>ASH</div>
    <div class="swatch" style="left:132px;top:187px;--c:#a5a7a9">FEVE GLOSS<br>WARM GREY</div>

    <div class="swatch dark-text" style="left:24px;top:223px;--c:#ffffff">FEVE GLOSS<br>WHITE</div>
    <div class="swatch" style="left:60px;top:223px;--c:#050505">FEVE GLOSS<br>BLACK</div>
    <div class="gloss-note" style="top:233px"><span class="range">COLOUR COATED SOLID ALUMINIUM</span><span class="finish">FEVE GLOSS 1.6MM</span></div>
  </div>
</section>

<!-- Sample box, dark version -->
<section class="scene" style="left:30px;top:727px;width:326px;height:210px;background:linear-gradient(180deg,#6c6f7e,#4b4e5d)">
  <div class="box-face dark" style="left:22px;top:36px;width:282px;height:110px">
    <div class="box-name" style="left:14px;top:12px">Kovo Slate</div>
    <div class="box-title" style="left:14px;top:54px">ALUMINIUM SAMPLES<strong>COLOUR BOX</strong></div>
    <div class="box-fine" style="left:14px;top:88px">Contains colour samples for PVDF and FEVE ranges</div>
    <div class="mosaic" style="left:160px;top:22px">
      <i style="--c:#fbb126"></i><i style="--c:#f7941d"></i><i style="--c:#f05a2a"></i><i style="--c:#da1f31"></i>
      <i style="--c:#fbe51a"></i><i style="--c:#9bc63f"></i><i style="--c:#3bad4a"></i><i style="--c:#0b8f51"></i>
      <i style="--c:#86bfdf"></i><i style="--c:#11938a"></i><i style="--c:#0a7d93"></i><i style="--c:#1287c9"></i>
      <i style="--c:#1745a0"></i><i style="--c:#232f7a"></i><i style="--c:#3d2a84"></i><i style="--c:#5e3591"></i>
    </div>
    <div class="label-panel"><div class="brand abs" style="left:7px;top:12px;font-size:7px">Kovo Slate</div></div>
  </div>
  <div class="scene-caption" style="top:183px">DARK VERISON</div>
</section>

<!-- Sample box, light version -->
<section class="scene" style="left:30px;top:937px;width:326px;height:213px;background:linear-gradient(180deg,#6c6f7e,#4b4e5d)">
  <div class="box-face light" style="left:22px;top:40px;width:282px;height:110px">
    <div class="box-name" style="left:14px;top:12px">Kovo Slate</div>
    <div class="box-title" style="left:14px;top:54px">ALUMINIUM SAMPLES<strong>COLOUR BOX</strong></div>
    <div class="mosaic" style="left:160px;top:22px">
      <i style="--c:#fbe51a"></i><i style="--c:#fbb126"></i><i style="--c:#f7941d"></i><i style="--c:#da1f31"></i>
      <i style="--c:#9bc63f"></i><i style="--c:#3bad4a"></i><i style="--c:#0b8f51"></i><i style="--c:#11938a"></i>
      <i style="--c:#86bfdf"></i><i style="--c:#0a7d93"></i><i style="--c:#1287c9"></i><i style="--c:#1745a0"></i>
      <i style="--c:#232f7a"></i><i style="--c:#3d2a84"></i><i style="--c:#5e3591"></i><i style="--c:#e3237a"></i>
    </div>
    <div class="dark-panel"><div class="brand abs" style="left:7px;top:12px;font-size:7px;color:#fff">Kovo Slate</div></div>
  </div>
  <div class="scene-caption" style="top:186px;justify-content:flex-end">LIGHT VERISON</div>
</section>

<!-- Brochure cover, flat -->
<section class="scene" style="left:405px;top:727px;width:224px;height:162px;background:linear-gradient(180deg,#8e909a,#a6a8b0)">
  <div class="abs" style="left:52px;top:18px;width:120px;height:126px;background:var(--paper);box-shadow:0 6px 12px rgba(0,0,0,.25)">
    <svg class="abs" style="left:0;top:40px" width="120" height="86" role="img" aria-label="Photograph of a glass office tower seen from below">
      <polygon points="18,86 60,10 102,86" fill="#c4c5c8"/>
    </svg>
    <div class="brand abs" style="left:62px;top:10px;font-size:7px">Kovo Slate</div>
  </div>
</section>

<!-- Sticker labels -->
<section class="scene" style="left:405px;top:982px;width:225px;height:168px;background:var(--cream)">
  <div class="sticker" style="left:22px;top:50px">
    <div class="brand">Kovo Slate</div>
    <div class="code">#FA877C</div>
    <div class="phone">1300 584 362</div>
  </div>
  <div class="option" style="left:45px;top:135px">OPTION 1</div>

  <div class="sticker" style="left:128px;top:50px">
    <div class="brand" style="right:auto;left:0;width:100%;text-align:center">Kovo Slate</div>
    <div class="code">#FA877C</div>
    <div class="hint">Product Code</div>
    <div class="phone" style="left:28px">1300 584 362</div>
  </div>
  <div class="option" style="left:151px;top:135px">OPTION 2</div>
</section>

</body>
</html>
```